Corvane Paintless Dent Removal

Our company works on vehicles removing dents using a highly skilled trade which the metal is massaged out with special tools without disturbing the original paint, hence paintless dent removal. Besides keeping the paint and metal original its also very environmentally friendly since no paint or toxic fillers are used. Also we we are one of the most experienced companies in the business with 25 years

Target Market(s)

Retail Automobile consumers, Auto Dealerships and Auto Body Shops

Industry/Entity Type

Auto Repair

Contact Information for Business Card

Dale Hollister
PO Box 518 Brookmere, NY 11962
631-555-0148
corvanepdr@mailbox-example.com
website corvanepdr.example
youtube corvane paintless dent removal
25 years of experience removing Dents, Dings and Hail Damage

Font styles to use
Serif
Sans Serif

Colors

Designer to choose colors to be used in the design.

Requirements
Must have
• I do like things that are simple but classy and somewhat bold, also I like my logo so that should be somewhat important

```html
<!DOCTYPE html>
<html lang="en">
<head>
<meta charset="UTF-8">
<title>Corvane Paintless Dent Removal – Business Card</title>
<link rel="stylesheet" href="https://fonts.googleapis.com/css2?family=Roboto:wght@400;500;700&display=swap">
<style>
  :root {
    --backdrop: #3b3b3d;
    --card: #1e1f21;
    --card-edge: #151617;
    --emboss: #2c2d30;
    --green: #7dc31f;
    --blue: #0f4ea0;
    --text: #e9e9e9;
    --muted: #c9c9c9;
    --red: #d9221c;
  }
  * { margin: 0; padding: 0; box-sizing: border-box; }
  html, body { width: 799px; height: 1200px; overflow: hidden; }
  body {
    background: var(--backdrop);
    font-family: "Roboto", Arial, sans-serif;
    position: relative;
  }
  .card {
    position: absolute;
    left: 60px;
    width: 679px;
    height: 388px;
    background: var(--card);
    border: 1px solid var(--card-edge);
    box-shadow: 0 14px 30px rgba(0,0,0,.45);
  }
  .card--front { top: 130px; }
  .card--back { top: 682px; }

  /* front */
  .front-mark {
    position: absolute;
    inset: 0;
    display: flex;
    align-items: center;
    justify-content: center;
    gap: 16px;
  }
  .front-mark__dot {
    width: 26px; height: 26px; border-radius: 50%;
    background: var(--emboss);
  }
  .front-mark__name {
    color: var(--emboss);
    font-weight: 700;
    font-size: 30px;
    letter-spacing: .5px;
  }

  /* back */
  .brand {
    position: absolute;
    top: 62px;
    right: 44px;
    display: flex;
    align-items: center;
    gap: 12px;
  }
  .brand__dot {
    width: 18px; height: 18px; border-radius: 50%;
    background: var(--blue);
  }
  .brand__name {
    color: var(--green);
    font-weight: 700;
    font-size: 22px;
    line-height: 1.15;
    text-align: left;
  }
  .person {
    position: absolute;
    left: 44px;
    top: 120px;
  }
  .person__name {
    color: var(--green);
    font-weight: 700;
    font-size: 30px;
  }
  .person__title {
    color: var(--muted);
    font-size: 15px;
    margin-top: 4px;
  }
  .contact-list {
    list-style: none;
    margin-top: 20px;
  }
  .contact-list li {
    display: flex;
    align-items: center;
    gap: 12px;
    color: var(--text);
    font-size: 16px;
    line-height: 26px;
  }
  .contact-list svg { width: 14px; height: 14px; fill: var(--green); flex: none; }
  .divider {
    position: absolute;
    left: 290px;
    right: 44px;
    top: 250px;
    height: 2px;
    background: var(--green);
  }
  .address {
    position: absolute;
    right: 44px;
    bottom: 34px;
    text-align: right;
    color: var(--text);
    font-size: 17px;
    line-height: 24px;
  }
  .address__video {
    display: inline-flex;
    align-items: center;
    gap: 10px;
  }
  .address__video-square {
    width: 18px; height: 14px; background: var(--red); border-radius: 2px;
  }
</style>
</head>
<body>

<section class="card card--front">
  <div class="front-mark">
    <span class="front-mark__dot"></span>
    <span class="front-mark__name">Corvane Paintless Dent Removal</span>
  </div>
</section>

<section class="card card--back">
  <div class="brand">
    <span class="brand__dot"></span>
    <span class="brand__name">Corvane<br>Paintless Dent Removal</span>
  </div>

  <div class="person">
    <h1 class="person__name">Dale Hollister</h1>
    <p class="person__title">Managing Director</p>
    <ul class="contact-list">
      <li>
        <svg viewBox="0 0 24 24" aria-hidden="true"><path d="M6.6 10.8a15 15 0 0 0 6.6 6.6l2.2-2.2c.3-.3.7-.4 1-.2 1.1.4 2.3.6 3.6.6.6 0 1 .4 1 1V20c0 .6-.4 1-1 1A17 17 0 0 1 3 4c0-.6.4-1 1-1h3.5c.6 0 1 .4 1 1 0 1.3.2 2.5.6 3.6.1.3 0 .7-.2 1z"/></svg>
        631-555-0148
      </li>
      <li>
        <svg viewBox="0 0 24 24" aria-hidden="true"><path d="M2 5h20v14H2zm2 2v.5l8 5 8-5V7zm0 2.8V17h16V9.8l-8 5z"/></svg>
        corvanepdr@mailbox-example.com
      </li>
      <li>
        <svg viewBox="0 0 24 24" aria-hidden="true"><path d="M12 2a10 10 0 1 0 0 20 10 10 0 0 0 0-20zm6.9 6h-3a15 15 0 0 0-1.3-3.9A8 8 0 0 1 18.9 8zM12 4c.8 1.2 1.5 2.5 1.9 4h-3.8c.4-1.5 1.1-2.8 1.9-4zM4.3 14a8 8 0 0 1 0-4h3.4a16 16 0 0 0 0 4zm.8 2h3a15 15 0 0 0 1.3 3.9A8 8 0 0 1 5.1 16zm3-8h-3a8 8 0 0 1 4.3-3.9C8.8 5.3 8.4 6.6 8.1 8zM12 20c-.8-1.2-1.5-2.5-1.9-4h3.8c-.4 1.5-1.1 2.8-1.9 4zm2.3-6H9.7a14 14 0 0 1 0-4h4.6a14 14 0 0 1 0 4zm.3 5.9c.6-1.2 1-2.5 1.3-3.9h3a8 8 0 0 1-4.3 3.9zm1.7-5.9a16 16 0 0 0 0-4h3.4a8 8 0 0 1 0 4z"/></svg>
        www.corvanepdr.example
      </li>
    </ul>
  </div>

  <div class="divider"></div>

  <div class="address">
    <p>PO Box 518 Brookmere,<br>NY 11962</p>
    <p class="address__video"><span class="address__video-square"></span>videohub.example/Dale Hollister</p>
  </div>
</section>

</body>
</html>
```